Web Design Project for Communications Agency

The design I need (PSD file) is for an agency offering specialised PR and communications services for customers in the healthcare sector.

OBJECTIVES OF THE WEBSITE:
1. To promote the agency's communication services
2. To position Solène Brivard as an industry leader, an expert in healthcare PR and communications by highlighting blogposts and social media.

WHAT I NEED:
1st, I need the design for the Home Page ONLY.
Once approved, I will need the other pages designed as well. (Here is prototype that we've already developed for the Website that will guide you in the design:
http://qorvelle.net/solenebrivard/)

VISUAL INSPIRATION
We want to give this Website a "Flat Design" look. Here are some websites for inspiration :
- http://tavrolinkworks.com/#!/process
- http://www.brindlemoss.co/
- http://quellaroft.com/

Also, reuse images found on the company's current Website :
http://www.solenebrivard.com/fr/index.html

HOMEPAGE MAIN ELEMENTS:
1. Main menu : 6 sections
Accueil | Agence | Services | Approche | Publications | Contact

2. Main Call To Action (big dark rectangle in prototype):
Can be slider or just an information bloc.

3. Publications récentes :
The 4 latest blog posts must be features on the homepage (will be linked with the "Publications" section)

4. Dynamic Footer :
Contains a Chirpline feed and a Subscribe to our Newsletter feature (revecez nos publications)

OTHER PAGES (to design once Homepage is approved)
- Agence (about us)
- Services (our team)
- Approche (our approach)
- Publications (blog articles)
- Contact (Contact us)

Industry/Entity Type

Communications

Requirements
Must have
• Please refer to prototype :
http://qorvelle.net/solenebrivard/
Must have ALL features present in prototype.

Also, must reuse this picture in the design : http://solenebrivard.com/static/images/home-big-box.jpg

Finally, you will find attached the company logo.

```html
<!DOCTYPE html>
<html lang="fr">
<head>
<meta charset="utf-8">
<title>Solène Brivard — Communications santé</title>
<link rel="stylesheet" href="https://fonts.googleapis.com/css2?family=Open+Sans:ital,wght@0,400;0,600;0,700;1,400&family=PT+Serif:wght@700&display=swap">
<style>
  :root{
    --red:#d0161f;
    --ink:#2b2b2b;
    --muted:#777;
    --page:#ececec;
    --card:#ffffff;
    --line:#dcdcdc;
    --footer:#1f1f1f;
    --footer-text:#cfcfcf;
    --button-dark:#2a2a2a;
    --accent-blue:#2b8fd6;
  }
  *{box-sizing:border-box;margin:0;padding:0}
  html,body{width:698px;height:1200px;overflow:hidden}
  body{font-family:"Open Sans",Arial,sans-serif;color:var(--ink);background:var(--page);position:relative}

  /* Header */
  .site-header{position:absolute;top:0;left:0;width:698px;height:72px;background:#fff}
  .brand{position:absolute;left:70px;top:18px;display:flex;align-items:center;gap:14px}
  .brand-name{font-family:"Open Sans",sans-serif;font-weight:700;font-size:18px;line-height:22px;color:var(--red)}
  .brand-tagline{font-size:7px;line-height:10px;font-weight:600;color:var(--muted);text-transform:uppercase;border-left:1px solid var(--line);padding-left:10px}
  .header-tools{position:absolute;right:70px;top:6px;display:flex;flex-direction:column;align-items:flex-end;gap:6px}
  .lang-select{font-size:8px;border:1px solid var(--line);padding:1px 14px 1px 4px;color:#555;background:#fff;position:relative}
  .lang-select::after{content:"";position:absolute;right:4px;top:5px;border:3px solid transparent;border-top-color:#777}
  .social{display:flex;gap:4px}
  .social span{width:14px;height:14px;border-radius:50%;background:#bdbdbd;display:block}

  /* Navigation */
  .main-nav{position:absolute;top:72px;left:0;width:698px;height:20px;background:var(--red)}
  .main-nav ul{list-style:none;display:flex;margin-left:70px;height:20px}
  .main-nav li{font-size:7.5px;font-weight:600;color:#fff;text-transform:uppercase;padding:0 11px;line-height:20px;border-right:1px solid rgba(255,255,255,.25)}
  .main-nav li:first-child{padding-left:4px}
  .main-nav li:last-child{border-right:none}

  /* Hero */
  .hero{position:absolute;top:92px;left:0;width:698px;height:252px;
    background:linear-gradient(90deg,#f4f4f4 0%,#e3e5e8 45%,#c9ced4 70%,#e9e9ea 100%)}
  .hero-photo{position:absolute;right:70px;top:0;width:200px;height:252px;
    background:linear-gradient(180deg,#dfe3e7 0%,#eef0f2 40%,#d5dbe0 100%)}
  .hero-title{position:absolute;left:70px;top:36px;width:270px;font-size:16px;font-weight:700;line-height:20px;color:#222}
  .hero-cta{position:absolute;left:70px;top:140px;width:160px;height:34px;background:var(--button-dark);color:#fff;
    font-size:10px;font-weight:700;text-transform:uppercase;display:flex;align-items:center;gap:10px;padding-left:12px}
  .circle-arrow{display:inline-block;flex:none}

  /* Publications */
  .publications{position:absolute;top:344px;left:0;width:698px;height:701px;background:var(--page)}
  .section-title{position:absolute;left:69px;top:22px;width:560px;height:32px;background:#fff}
  .section-title h2{font-size:15px;font-weight:400;color:#222;line-height:30px;padding-left:6px;display:inline-block;border-bottom:2px solid var(--red);height:32px}
  .post{position:absolute;left:69px;width:560px;height:138px;background:var(--card);border-bottom:1px solid var(--line)}
  .post-thumb{position:absolute;left:6px;top:8px;width:86px;height:66px}
  .post-title{position:absolute;left:100px;top:10px;font-family:"PT Serif",serif;font-weight:700;font-size:9px;color:#222}
  .post-date{position:absolute;right:10px;top:10px;font-size:8px;font-style:italic;color:#444}
  .post-excerpt{position:absolute;left:100px;top:26px;width:450px;font-size:7px;line-height:10px;color:var(--muted)}
  .post-link{position:absolute;left:6px;top:112px;font-size:8px;color:var(--red);display:flex;align-items:center;gap:5px}

  /* Footer */
  .site-footer{position:absolute;top:1045px;left:0;width:698px;height:155px;background:var(--footer);color:var(--footer-text)}
  .feed{position:absolute;left:70px;top:14px;width:300px}
  .feed-name{font-size:16px;font-weight:600;color:#fff;display:flex;align-items:center;gap:7px;line-height:20px}
  .feed-name i{width:10px;height:10px;border-radius:50%;background:var(--accent-blue);display:block}
  .feed-text{font-size:7px;line-height:10px;margin-top:8px;width:220px}
  .feed-tags{font-size:7px;font-weight:700;color:#fff;margin-top:3px;word-spacing:6px}
  .feed-button{margin-top:8px;display:inline-block;background:var(--accent-blue);color:#fff;font-size:7px;font-weight:600;padding:3px 9px;border-radius:2px}
  .newsletter{position:absolute;left:448px;top:14px;width:180px}
  .newsletter h3{font-size:10px;font-weight:600;color:#fff;text-transform:uppercase;margin-bottom:8px}
  .field{width:130px;height:15px;background:#fff;color:#999;font-size:7px;padding-left:5px;line-height:15px;margin-bottom:6px}
  .subscribe{display:inline-block;background:var(--red);color:#fff;font-size:7px;font-weight:600;padding:3px 10px}
  .footer-bar{position:absolute;left:70px;right:70px;bottom:12px;border-top:1px solid #3a3a3a;padding-top:8px;display:flex;justify-content:space-between;font-size:7px;color:#999}
</style>
</head>
<body>

<header class="site-header">
  <div class="brand">
    <div class="brand-name">Solène Brivard</div>
    <div class="brand-tagline">Secteur d'affaires<br>Affaires publiques</div>
  </div>
  <div class="header-tools">
    <div class="lang-select">English</div>
    <div class="social"><span></span><span></span><span></span><span></span><span></span></div>
  </div>
</header>

<nav class="main-nav">
  <ul>
    <li>Accueil</li><li>Agence</li><li>Services</li><li>Approche</li><li>Publications</li><li>Contact</li>
  </ul>
</nav>

<section class="hero">
  <div class="hero-photo" role="img" aria-label="Photo d'un médecin souriant en blouse blanche avec stéthoscope, bras croisés, sur fond de ville floue"></div>
  <h1 class="hero-title">Cabinet-conseil en communications et affaires publiques spécialisé dans le secteur de la santé.</h1>
  <div class="hero-cta">
    <svg class="circle-arrow" width="18" height="18" viewBox="0 0 18 18"><circle cx="9" cy="9" r="9" fill="#d0161f"/><path d="M7 5l4 4-4 4" stroke="#fff" stroke-width="2" fill="none"/></svg>
    En savoir plus
  </div>
</section>

<main class="publications">
  <div class="section-title"><h2>Publication Récentes</h2></div>

  <article class="post" style="top:60px">
    <div class="post-thumb" role="img" aria-label="Photo d'une équipe médicale au bloc opératoire" style="background:linear-gradient(135deg,#7fb8c4,#cfe3e6)"></div>
    <h3 class="post-title">Titre de la publication</h3>
    <span class="post-date">23 juillet 2013</span>
    <p class="post-excerpt">Cette publication présente les enjeux récents en communication santé, les tendances observées auprès des établissements et des conseils pratiques pour mieux joindre les patients, les professionnels et les décideurs publics. Une analyse claire et concise pour orienter vos prochaines actions. Consultez l'article complet pour découvrir nos recommandations détaillées et les exemples concrets.</p>
    <a class="post-link"><span>Article complet</span><svg width="10" height="10" viewBox="0 0 10 10"><circle cx="5" cy="5" r="4.5" fill="none" stroke="#d0161f"/><path d="M4 3l2 2-2 2" stroke="#d0161f" fill="none"/></svg></a>
  </article>

  <article class="post" style="top:222px">
    <div class="post-thumb" role="img" aria-label="Photo d'une chercheuse en laboratoire avec éprouvettes" style="background:linear-gradient(135deg,#9fc6de,#e6eef3)"></div>
    <h3 class="post-title">Titre de la publication</h3>
    <span class="post-date">23 juillet 2013</span>
    <p class="post-excerpt">Cette publication présente les enjeux récents en communication santé, les tendances observées auprès des établissements et des conseils pratiques pour mieux joindre les patients, les professionnels et les décideurs publics. Une analyse claire et concise pour orienter vos prochaines actions. Consultez l'article complet pour découvrir nos recommandations détaillées et les exemples concrets.</p>
    <a class="post-link"><span>Article complet</span><svg width="10" height="10" viewBox="0 0 10 10"><circle cx="5" cy="5" r="4.5" fill="none" stroke="#d0161f"/><path d="M4 3l2 2-2 2" stroke="#d0161f" fill="none"/></svg></a>
  </article>

  <article class="post" style="top:384px">
    <div class="post-thumb" role="img" aria-label="Illustration d'une croix médicale rouge en relief" style="background:linear-gradient(135deg,#e9e9e9,#d9a0a0)"></div>
    <h3 class="post-title">Titre de la publication</h3>
    <span class="post-date">23 juillet 2013</span>
    <p class="post-excerpt">Cette publication présente les enjeux récents en communication santé, les tendances observées auprès des établissements et des conseils pratiques pour mieux joindre les patients, les professionnels et les décideurs publics. Une analyse claire et concise pour orienter vos prochaines actions. Consultez l'article complet pour découvrir nos recommandations détaillées et les exemples concrets.</p>
    <a class="post-link"><span>Article complet</span><svg width="10" height="10" viewBox="0 0 10 10"><circle cx="5" cy="5" r="4.5" fill="none" stroke="#d0161f"/><path d="M4 3l2 2-2 2" stroke="#d0161f" fill="none"/></svg></a>
  </article>

  <article class="post" style="top:546px">
    <div class="post-thumb" role="img" aria-label="Photo d'un groupe de médecins dans un couloir d'hôpital" style="background:linear-gradient(135deg,#b7c9d6,#eef2f5)"></div>
    <h3 class="post-title">Titre de la publication</h3>
    <span class="post-date">23 juillet 2013</span>
    <p class="post-excerpt">Cette publication présente les enjeux récents en communication santé, les tendances observées auprès des établissements et des conseils pratiques pour mieux joindre les patients, les professionnels et les décideurs publics. Une analyse claire et concise pour orienter vos prochaines actions. Consultez l'article complet pour découvrir nos recommandations détaillées et les exemples concrets.</p>
    <a class="post-link"><span>Article complet</span><svg width="10" height="10" viewBox="0 0 10 10"><circle cx="5" cy="5" r="4.5" fill="none" stroke="#d0161f"/><path d="M4 3l2 2-2 2" stroke="#d0161f" fill="none"/></svg></a>
  </article>
</main>

<footer class="site-footer">
  <div class="feed">
    <div class="feed-name"><i></i>Chirpline</div>
    <p class="feed-text">Le nouveau guide des communications en santé est maintenant en ligne. Découvrez nos conseils pour vos campagnes.</p>
    <p class="feed-tags">#Santé #Relations #Com</p>
    <span class="feed-button">Suivre</span>
  </div>
  <div class="newsletter">
    <h3>Recevez nos publications</h3>
    <div class="field">Votre nom</div>
    <div class="field">Votre courriel</div>
    <span class="subscribe">Abonnez-vous</span>
  </div>
  <div class="footer-bar">
    <span>© Solène Brivard. Tous droits réservés.</span>
    <span>#Santé#com</span>
  </div>
</footer>

</body>
</html>
```